I need a complete stationary pack for a real estate office that sells and manages residential proper

We need a stationary design pack for my real estate office called ‘brightkeyhomes’ that is in Queensland Australia. My offices are both in suburban and coastal locations in the south west corner of Queensland at the Coral Bay Shore and Brisbane.
We predominately manage real estate on behalf of owners and sell property in the residential sector.
I have attached a copy of our existing design of my business card and do like the current concept/layout. In saying this you may be able to use this existing theme across to the other items required or see opportunity on how to improve what I have already.
I would like to see concepts for the following products:
- Letterhead
- Fax header
- Business cards
- Email signature
- With complements slips and
- Envelopes
I have attached our current logo that was designed by Artfolder and the font is Prelo.

I am looking for a contemporary design that is professional and reflects trust and professionalism. I am currently using the logo with a black background on some material as per the following link

http://www.plotlisting.com.au/property/for-sale/house/qld/merridale/?adid=4827305118&sp=7

I have posted another job 517362 for signage and the company car signage done too if you are interested.

Please do not hesitate to contact me should you have any questions. Thank you.

Target Market(s)

Western speaking people aged from 25 to 60 from modest backgrounds to well off individuals

Industry/Entity Type

Real Estate

Requirements
Must have
• Professional in appearance, show a mature and trustworthy image
Should not have
• As there is good colour with the logo, i am do not want over the top designs or colours

```html
<!DOCTYPE html>
<html lang="en">
<head>
<meta charset="utf-8">
<title>brightkeyhomes business card</title>
<link rel="stylesheet" href="https://fonts.googleapis.com/css2?family=Open+Sans:wght@400;600;700&display=swap">
<style>
  :root {
    --page-bg: #e9e6e1;
    --card-black: #0d0d0d;
    --card-black-soft: #232323;
    --card-white: #ffffff;
    --ink: #2b3340;
    --ink-soft: #4a4f57;
    --muted: #9a9a9a;
    --accent-red: #d7262b;
    --accent-green: #3a9b3e;
    --photo-sky: #6f9cc4;
    --photo-suit: #2e3238;
  }
  * { box-sizing: border-box; margin: 0; padding: 0; }
  html, body {
    width: 1200px; height: 1024px; overflow: hidden;
    background: var(--page-bg);
    font-family: "Open Sans", Arial, sans-serif;
  }
  .canvas {
    position: relative; width: 1200px; height: 1024px;
  }
  .card {
    position: absolute; left: 200px; width: 800px; height: 457px;
    border-radius: 34px; overflow: hidden;
    box-shadow: 0 6px 18px rgba(0,0,0,0.18);
  }
  .card-front {
    top: 36px;
    background: linear-gradient(135deg, var(--card-black-soft) 0%, var(--card-black) 60%);
  }
  .card-back {
    top: 531px;
    background: var(--card-white);
  }
  .front-brand {
    position: absolute; left: 56px; bottom: 92px;
    display: flex; align-items: center; gap: 16px;
  }
  .brand-dot {
    width: 30px; height: 30px; border-radius: 50%;
    background: var(--accent-green);
  }
  .front-name {
    font-size: 62px; font-weight: 600; color: #ffffff; letter-spacing: -1px;
  }
  .front-url {
    position: absolute; left: 104px; bottom: 56px;
    font-size: 20px; color: var(--muted); letter-spacing: 0.3px;
  }
  .portrait {
    position: absolute; left: 34px; top: 34px; width: 312px; height: 290px;
    background: linear-gradient(180deg, var(--photo-sky) 0%, #9ab8d2 55%, var(--photo-suit) 56%, #1f2226 100%);
  }
  .back-brand {
    position: absolute; left: 388px; top: 48px;
    display: flex; align-items: center; gap: 14px;
  }
  .back-brand .brand-dot { width: 40px; height: 40px; }
  .back-name {
    font-size: 44px; font-weight: 600; color: var(--ink); letter-spacing: -0.5px;
  }
  .contact {
    position: absolute; left: 390px; top: 150px; line-height: 1.35;
  }
  .person-name { font-size: 27px; font-weight: 700; color: var(--accent-red); }
  .person-role { font-size: 18px; color: var(--accent-green); }
  .person-mobile { font-size: 19px; color: var(--ink-soft); margin-bottom: 8px; }
  .contact-line { font-size: 17px; color: var(--ink-soft); }
  .contact-line .label { color: var(--accent-red); font-weight: 600; margin-right: 4px; }
</style>
</head>
<body>
<div class="canvas">
  <section class="card card-front">
    <div class="front-brand">
      <span class="brand-dot"></span>
      <span class="front-name">brightkeyhomes</span>
    </div>
    <div class="front-url">www.brightkeyhomes.com.au</div>
  </section>

  <section class="card card-back">
    <div class="portrait" role="img" aria-label="Portrait photograph of the principal in a dark suit against a coastal sky"></div>
    <div class="back-brand">
      <span class="brand-dot"></span>
      <span class="back-name">brightkeyhomes</span>
    </div>
    <div class="contact">
      <div class="person-name">Marcus Delane</div>
      <div class="person-role">Principal</div>
      <div class="person-mobile">0412 555 207</div>
      <div class="contact-line"><span class="label">P:</span>07 5550 1846</div>
      <div class="contact-line"><span class="label">E:</span>marcus@brightkeyhomes.com.au</div>
      <div class="contact-line"><span class="label">A:</span>shop 4, 52 harbour parade merridale qld 4571</div>
    </div>
  </section>
</div>
</body>
</html>
```